BOLD & MINIMALIST DESIGN NEEDED

We want a very bold but minimalistic business card design that is impactful and utilizes both sides of the business card. Our current logo is included for your use.

We want bold fonts and good use of negative space. We don't want the logo to overpower the design.

Target Market(s)

Professionals who are building new commercial buildings.

Industry/Entity Type

Construction

Contact Information for Business Card

Name, Title, email, office phone, cell phone, website

Font styles to use
Serif
Sans Serif

Requirements
Must have
• Bold design!

```html
<!DOCTYPE html>
<html lang="en">
<head>
<meta charset="utf-8">
<title>Talvenor Design + Build – Business Card</title>
<link href="https://fonts.googleapis.com/css2?family=Poppins:wght@400;600;700&display=swap" rel="stylesheet">
<style>
  :root {
    --page-bg: #e9e6e1;
    --card-white: #ffffff;
    --ink: #1c1c1c;
    --ink-soft: #3a3a3a;
    --brand-green: #8cc63f;
    --green-light: #e2f0cf;
    --green-mid: #b7da86;
    --green-deep: #a3cd68;
    --card-shadow: rgba(0, 0, 0, 0.35);
  }
  * { margin: 0; padding: 0; box-sizing: border-box; }
  html, body {
    width: 916px; height: 1200px; overflow: hidden;
    background: var(--page-bg);
    font-family: "Poppins", Arial, sans-serif;
    color: var(--ink);
  }
  .card {
    position: absolute;
    left: 73px;
    width: 770px;
    height: 460px;
    border-radius: 22px;
    box-shadow: 0 8px 18px var(--card-shadow);
    overflow: hidden;
  }
  .card--front { top: 108px; background: var(--card-white); }
  .card--back {
    top: 640px;
    height: 462px;
    background: linear-gradient(135deg, var(--green-light) 0%, var(--green-mid) 60%, var(--green-deep) 100%);
  }

  /* Front */
  .brand-name {
    position: absolute; left: 38px; top: 60px;
    font-weight: 700; color: var(--ink);
    line-height: 1;
  }
  .brand-name__main { display: block; font-size: 50px; letter-spacing: 1px; }
  .brand-name__sub { display: block; font-size: 21px; letter-spacing: 6px; margin-top: 8px; padding-left: 20px; }

  .person { position: absolute; left: 31px; top: 220px; }
  .person__name { font-size: 27px; font-weight: 600; color: var(--brand-green); line-height: 1.1; }
  .person__title { font-size: 16px; color: var(--ink-soft); margin-top: 6px; }

  .contact-list { position: absolute; left: 31px; top: 330px; list-style: none; }
  .contact-list li {
    display: flex; align-items: center; gap: 9px;
    font-size: 16.5px; color: var(--ink-soft); height: 25.5px;
  }
  .contact-list svg { width: 17px; height: 17px; fill: var(--brand-green); flex: none; }

  /* Back */
  .back-brand {
    position: absolute; left: 0; right: 0; top: 95px;
    display: flex; flex-direction: column; align-items: center;
  }
  .back-brand__mark { width: 120px; height: 120px; background: var(--ink); margin-bottom: 42px; }
  .back-brand__name { font-weight: 700; color: var(--ink); line-height: 1; text-align: center; }
  .back-brand__main { display: block; font-size: 72px; letter-spacing: 2px; }
  .back-brand__sub { display: block; font-size: 27px; letter-spacing: 8px; margin-top: 8px; }
</style>
</head>
<body>

<section class="card card--front" aria-label="Business card front">
  <div class="brand-name">
    <span class="brand-name__main">TALVENOR</span>
    <span class="brand-name__sub">DESIGN + BUILD</span>
  </div>

  <div class="person">
    <p class="person__name">Marlen Voskuil</p>
    <p class="person__title">CEO &amp; Founder</p>
  </div>

  <ul class="contact-list">
    <li>
      <svg viewBox="0 0 24 24" aria-hidden="true"><path d="M6.6 10.8a15.1 15.1 0 0 0 6.6 6.6l2.2-2.2a1 1 0 0 1 1-.25 11.4 11.4 0 0 0 3.6.57 1 1 0 0 1 1 1V20a1 1 0 0 1-1 1A17 17 0 0 1 3 4a1 1 0 0 1 1-1h3.5a1 1 0 0 1 1 1c0 1.25.2 2.45.57 3.6a1 1 0 0 1-.25 1z"/></svg>
      (303) 555-0148
    </li>
    <li>
      <svg viewBox="0 0 24 24" aria-hidden="true"><path d="M3 8c0-2 4-4 9-4s9 2 9 4v2h-5V8H8v2H3z M6 12h12l2 8H4z"/></svg>
      1-800-555-0192
    </li>
    <li>
      <svg viewBox="0 0 24 24" aria-hidden="true"><path d="M2 6v12h20V6l-10 7.5z M3 5h18l-9 6.8z"/></svg>
      hello@talvenorbuild.com
    </li>
    <li>
      <svg viewBox="0 0 24 24" aria-hidden="true"><path d="M12 2a10 10 0 1 0 0 20 10 10 0 0 0 0-20zm6.9 6h-3a15 15 0 0 0-1.3-3.9A8 8 0 0 1 18.9 8zM12 4a13 13 0 0 1 1.9 4h-3.8A13 13 0 0 1 12 4zM4.3 14a8 8 0 0 1 0-4h3.4a16 16 0 0 0 0 4zm.8 2h3a15 15 0 0 0 1.3 3.9A8 8 0 0 1 5.1 16zm3-8h-3a8 8 0 0 1 4.3-3.9A15 15 0 0 0 8.1 8zM12 20a13 13 0 0 1-1.9-4h3.8A13 13 0 0 1 12 20zm2.3-6H9.7a14 14 0 0 1 0-4h4.6a14 14 0 0 1 0 4zm.3 5.9a15 15 0 0 0 1.3-3.9h3a8 8 0 0 1-4.3 3.9zm1.7-5.9a16 16 0 0 0 0-4h3.4a8 8 0 0 1 0 4z"/></svg>
      www.talvenorbuild.com
    </li>
  </ul>
</section>

<section class="card card--back" aria-label="Business card back">
  <div class="back-brand">
    <div class="back-brand__mark" aria-hidden="true"></div>
    <div class="back-brand__name">
      <span class="back-brand__main">TALVENOR</span>
      <span class="back-brand__sub">DESIGN + BUILD</span>
    </div>
  </div>
</section>

</body>
</html>
```